Dietitian needs awesome business card

I need a contemporary design that's eye catching but professional.
My card is to given to doctors, specialists and patients alike.
I manage patients with chronic diseases
I have uploaded my logo and current business card, I would also like the other Certified Clinical Nutritionist logo incorporated into the design

Target Market(s)

Doctors, specialists and patients

Industry/Entity Type

Healthcare

Contact Information for Business Card

www.brightfieldnutrition.com.au
Ph: 0427 561 903
Fax: 6457 2183
email: marcus.k.diet@fernmail.com
Space on the back of the card with: Appointment date, Appointment time and appointment location

Font styles to use
Serif

Colors
fbee3e
876aae
ffc214

Requirements
Must have
• My Logo
• Certified Clinical Nutritionist Logo
• My 4 locations - Pinebrook Medical Centre, North Corrin Health, Hollis Medical, Ashcombe Doctors Surgery
Nice to have
• I like the colours in my current business card

```html
<!DOCTYPE html>
<html lang="en">
<head>
<meta charset="utf-8">
<title>Brightfield Nutrition &amp; Dietetics — Business Card</title>
<link rel="stylesheet" href="https://fonts.googleapis.com/css2?family=Marcellus&family=Alike&display=swap">
<style>
  :root {
    --bg: #e4e6e8;
    --card: #ffffff;
    --lime: #c3dd3a;
    --green: #8cc63f;
    --blue: #1f63b5;
    --navy: #0d3f7d;
    --text-blue: #2a6fc4;
    --ink: #3b3f44;
    --label: #8a8e93;
    --badge: #f07f2a;
  }
  * { box-sizing: border-box; margin: 0; padding: 0; }
  html, body { width: 1200px; height: 900px; overflow: hidden; }
  body { background: var(--bg); font-family: "Alike", Georgia, serif; }

  .card {
    position: absolute; top: 80px; width: 420px; height: 740px;
    background: var(--card); overflow: hidden;
    box-shadow: 0 10px 30px rgba(0,0,0,.18);
  }
  .card--front { left: 150px; }
  .card--back { left: 630px; }
  .card__art { position: absolute; inset: 0; width: 420px; height: 740px; }

  /* front */
  .brand { position: absolute; left: 40px; top: 300px; display: flex; align-items: center; gap: 14px; }
  .brand__dot { width: 46px; height: 46px; border-radius: 50%; background: var(--green); flex: none; }
  .brand__name { font-family: "Marcellus", Georgia, serif; color: var(--text-blue); font-size: 30px; line-height: 1.05; }
  .brand__name small { display: block; font-size: 17px; letter-spacing: .5px; }

  .person { position: absolute; left: 40px; top: 395px; width: 330px; }
  .person__name { font-family: "Marcellus", Georgia, serif; color: var(--text-blue); font-size: 27px; padding-bottom: 10px; border-bottom: 1px solid #b9bcc0; }

  .contacts { position: absolute; left: 40px; top: 462px; list-style: none; }
  .contacts li { display: flex; align-items: center; gap: 12px; font-size: 16px; color: var(--ink); height: 27px; }
  .contacts svg { width: 18px; height: 18px; flex: none; }

  .badge { position: absolute; left: 40px; top: 585px; width: 150px; height: 60px; background: var(--badge); border-radius: 6px; }

  /* back */
  .appointment { position: absolute; left: 40px; top: 55px; width: 340px; }
  .appointment__title { font-family: "Marcellus", Georgia, serif; color: var(--text-blue); font-size: 30px; letter-spacing: 1px; margin-bottom: 24px; }
  .field { display: flex; align-items: baseline; gap: 8px; font-size: 18px; color: var(--label); margin-bottom: 22px; }
  .field__line { flex: 1; border-bottom: 2px dotted #a7abb0; }

  .locations { position: absolute; left: 40px; top: 325px; }
  .locations__title { font-family: "Marcellus", Georgia, serif; color: var(--green); font-size: 22px; letter-spacing: .5px; margin-bottom: 14px; }
  .locations ul { list-style: none; }
  .locations li { display: flex; align-items: center; gap: 12px; font-size: 17px; color: var(--text-blue); margin-bottom: 12px; }
  .checkbox { width: 20px; height: 20px; border: 1.5px solid #555; flex: none; }
</style>
</head>
<body>

<section class="card card--front" aria-label="Business card front">
  <svg class="card__art" viewBox="0 0 420 740">
    <defs>
      <linearGradient id="frontTop" x1="0" y1="0" x2="1" y2="1">
        <stop offset="0" stop-color="#c3dd3a"/>
        <stop offset="1" stop-color="#8cc63f"/>
      </linearGradient>
      <linearGradient id="frontBottom" x1="0" y1="0" x2="1" y2="1">
        <stop offset="0" stop-color="#c3dd3a"/>
        <stop offset=".6" stop-color="#8cc63f"/>
        <stop offset="1" stop-color="#0d3f7d"/>
      </linearGradient>
    </defs>
    <path role="img" aria-label="Decorative green wave artwork" d="M130,0 H420 V240 C360,200 250,150 130,0 Z" fill="url(#frontTop)"/>
    <path role="img" aria-label="Decorative green and blue wave artwork" d="M0,712 C220,700 370,620 420,500 V740 H0 Z" fill="url(#frontBottom)"/>
  </svg>

  <div class="brand">
    <span class="brand__dot"></span>
    <p class="brand__name">Brightfield<small>Nutrition &amp; Dietetics</small></p>
  </div>

  <div class="person"><p class="person__name">Marcus Kellaway</p></div>

  <ul class="contacts">
    <li><svg viewBox="0 0 18 18"><rect x="3" y="2" width="12" height="6" fill="none" stroke="var(--blue)" stroke-width="1.5"/><rect x="1" y="8" width="16" height="8" rx="1" fill="var(--blue)"/></svg>6457 2183</li>
    <li><svg viewBox="0 0 18 18"><path d="M2,6 C2,3 16,3 16,6 L13,8 L11,6 H7 L5,8 Z M4,9 H14 L15,16 H3 Z" fill="var(--blue)"/></svg>0427 561 903</li>
    <li><svg viewBox="0 0 18 18"><rect x="1" y="4" width="16" height="11" rx="1" fill="var(--blue)"/><path d="M1.5,5 L9,11 L16.5,5" fill="none" stroke="#fff" stroke-width="1.3"/></svg>marcus.k.diet@fernmail.com</li>
    <li><svg viewBox="0 0 18 18"><circle cx="9" cy="9" r="7" fill="none" stroke="var(--blue)" stroke-width="1.6"/><ellipse cx="9" cy="9" rx="3" ry="7" fill="none" stroke="var(--blue)" stroke-width="1.2"/><path d="M2,9 H16" stroke="var(--blue)" stroke-width="1.2"/></svg>www.brightfieldnutrition.com.au</li>
  </ul>

  <div class="badge" role="img" aria-label="Certified Clinical Nutritionist badge"></div>
</section>

<section class="card card--back" aria-label="Business card back">
  <svg class="card__art" viewBox="0 0 420 740">
    <defs>
      <linearGradient id="backBottom" x1="0" y1="0" x2="1" y2="1">
        <stop offset="0" stop-color="#c3dd3a"/>
        <stop offset=".6" stop-color="#8cc63f"/>
        <stop offset="1" stop-color="#0d3f7d"/>
      </linearGradient>
    </defs>
    <path role="img" aria-label="Decorative green and blue wave artwork" d="M0,610 C180,600 355,510 420,310 V740 H0 Z" fill="url(#backBottom)"/>
  </svg>

  <div class="appointment">
    <h2 class="appointment__title">APPOINTMENT</h2>
    <p class="field">Date:<span class="field__line"></span></p>
    <p class="field">Time:<span class="field__line"></span></p>
    <p class="field">Date:<span class="field__line"></span></p>
    <p class="field">Time:<span class="field__line"></span></p>
  </div>

  <div class="locations">
    <h3 class="locations__title">APPOINTMENT LOCATION</h3>
    <ul>
      <li><span class="checkbox"></span>North Corrin Health</li>
      <li><span class="checkbox"></span>Hollis Medical</li>
      <li><span class="checkbox"></span>Pinebrook Medical Centre</li>
      <li><span class="checkbox"></span>Ashcombe Doctors Surgery</li>
    </ul>
  </div>
</section>

</body>
</html>
```